sydney wedding photography business needs a business card design

we need a business card design for a sydney based wedding photography and videography business. our business name is :golden hour studio and film. our target clients are 24-35 yrs female. our style is candid, organic, natural, dynamic. we are a team of young photographers and videographers, and help brides to create memories that they will cherish for the rest of their lives. the logo will be provided. we want an elegant design that reflects our style, and also want to give a great impression to our clients that we are one of the best studios in sydney and our brand means quality and premium service.

Target Market(s)

bride to be, 24-35 years old, living in sydney and surrunding areas

Industry/Entity Type

Wedding Photography

Contact Information for Business Card

address: 57 tarrant street, glenmore nsw 2047
mobile: 0431872259
phone: (02) 9163 2408
info@tidewillowstudio.net.au
www.tidewillowstudio.net.au
facebook:tidewillowweddings
instagram:tidewillowweddings

Font styles to use
Serif
Sans Serif

Requirements
Nice to have
• maybe add my slogan"memories beyond eternity" if the layout looks good
Should not have
• no black color, not good idea for wedding biz card

```html
<!DOCTYPE html>
<html lang="en">
<head>
<meta charset="utf-8">
<title>Golden Hour Studio and Film – Business Card</title>
<link rel="stylesheet" href="https://fonts.googleapis.com/css2?family=Montserrat:wght@400;500;600&display=swap">
<style>
  :root {
    --backdrop: #ddd5c7;
    --card-light: #fbf7ee;
    --card-warm: #efe4cf;
    --gold: #c8941b;
    --gold-deep: #a8780e;
    --gold-light: #ecc75a;
    --text-main: #5a4632;
    --text-soft: #7d6a55;
    --rule: #cdbb9c;
  }
  * { margin: 0; padding: 0; box-sizing: border-box; }
  html, body {
    width: 1200px; height: 843px; overflow: hidden;
    background: var(--backdrop);
    font-family: "Montserrat", sans-serif;
  }
  .canvas {
    width: 1200px; height: 843px;
    display: flex; align-items: center; justify-content: center; gap: 40px;
  }
  .card {
    position: relative;
    width: 560px; height: 311px;
    border-radius: 4px;
    overflow: hidden;
    background: linear-gradient(135deg, var(--card-light) 0%, var(--card-warm) 100%);
    box-shadow: 0 10px 26px rgba(90, 70, 50, 0.22);
  }

  /* Back side */
  .card-back .streak {
    position: absolute; inset: 0; width: 100%; height: 100%;
  }
  .back-brand {
    position: absolute; left: 0; right: 0; top: 112px;
    display: flex; align-items: center; justify-content: center; gap: 14px;
  }
  .back-brand .dot {
    width: 16px; height: 16px; border-radius: 50%; background: var(--gold);
  }
  .back-brand .brand-name {
    color: var(--gold); font-weight: 600; font-size: 22px;
    letter-spacing: 0.06em; text-transform: uppercase;
  }

  /* Front side */
  .front-brand {
    position: absolute; right: 34px; top: 48px;
    color: var(--gold); font-weight: 600; text-transform: uppercase; text-align: right;
  }
  .front-brand .brand-main {
    display: block; font-size: 26px; line-height: 1.1; letter-spacing: 0.05em;
  }
  .front-brand .brand-sub {
    display: block; font-size: 10px; letter-spacing: 0.42em; margin-top: 6px;
    margin-right: -0.42em;
  }
  .person {
    position: absolute; left: 30px; top: 104px;
  }
  .person-name { color: var(--gold); font-size: 15px; font-weight: 500; }
  .person-role { color: var(--text-main); font-size: 11px; margin-top: 3px; }
  .divider {
    position: absolute; left: 30px; right: 30px; top: 148px;
    height: 1px; background: var(--rule);
  }
  .contacts {
    position: absolute; left: 30px; top: 160px;
    list-style: none;
  }
  .contacts li {
    display: flex; align-items: center; gap: 8px;
    color: var(--text-main); font-size: 11.5px; line-height: 1.65;
  }
  .contacts svg { width: 12px; height: 12px; flex: none; }
  .location {
    position: absolute; right: 34px; bottom: 28px;
    color: var(--text-soft); font-size: 11.5px; line-height: 1.5; text-align: right;
    font-style: normal;
  }
  .gold-band {
    position: absolute; left: 0; right: 0; bottom: 0; height: 14px;
    background: linear-gradient(90deg, var(--gold-deep), var(--gold-light) 50%, var(--gold-deep));
  }
</style>
</head>
<body>
<main class="canvas">

  <section class="card card-back" aria-label="Card back">
    <svg class="streak" viewBox="0 0 560 311" aria-hidden="true">
      <line x1="150" y1="235" x2="520" y2="178" stroke="#c8941b" stroke-width="1" opacity="0.7"/>
    </svg>
    <div class="back-brand">
      <span class="dot"></span>
      <span class="brand-name">golden hour studio and film</span>
    </div>
  </section>

  <section class="card card-front" aria-label="Card front">
    <div class="front-brand">
      <span class="brand-main">golden hour</span>
      <span class="brand-sub">studio and film</span>
    </div>

    <div class="person">
      <div class="person-name">Liam Carter</div>
      <div class="person-role">President</div>
    </div>

    <div class="divider"></div>

    <ul class="contacts">
      <li>
        <svg viewBox="0 0 24 24" aria-hidden="true"><path fill="#c8941b" d="M6.6 10.8a15.1 15.1 0 0 0 6.6 6.6l2.2-2.2c.3-.3.7-.4 1-.2 1.1.4 2.3.6 3.6.6.6 0 1 .4 1 1V20c0 .6-.4 1-1 1C10.6 21 3 13.4 3 4c0-.6.4-1 1-1h3.5c.6 0 1 .4 1 1 0 1.3.2 2.5.6 3.6.1.3 0 .7-.2 1z"/></svg>
        (02) 9163 2408
      </li>
      <li>
        <svg viewBox="0 0 24 24" aria-hidden="true"><rect x="6" y="2" width="12" height="20" rx="2" fill="#c8941b"/><rect x="8" y="5" width="8" height="12" fill="#fbf7ee"/></svg>
        (04) 3187 2259
      </li>
      <li>
        <svg viewBox="0 0 24 24" aria-hidden="true"><rect x="2" y="5" width="20" height="14" rx="1.5" fill="#c8941b"/><path d="M3 6l9 7 9-7" fill="none" stroke="#fbf7ee" stroke-width="1.8"/></svg>
        info@tidewillowstudio.net.au
      </li>
    </ul>

    <address class="location">
      57 tarrant street<br>
      glenmore nsw 2047<br>
      www.tidewillowstudio.net.au
    </address>

    <div class="gold-band"></div>
  </section>

</main>
</body>
</html>
```